Restaurant Finder Website Design

I need to create a website that will help people find restaurants around a zip code or address.

I would like to have a very clean and simple design. I will need a design for the homepage, that should be very clean and simple to use. its where the users will launch their search. I am thinking something like tavuro like.. big search field with a very clean page where users can create an account or restaurants subscribe to the service.

Also need the design of the search results page, I would like to display a big map with the results and a list on the side or the bottom of the map.

Also need a profile page for the users that sign up to the site.

Mostly what I need are guidelines and color coordinated elements, like a general layout and buttons that work together. I would like to know what the action buttons and elements should look like. Because its going to have some more detail pages.

Target Market(s)

People in general, mainly people that work at an office and have to find a place for lunch every day.

Industry/Entity Type

Restaurant

Number of Pages Required

4 page

Font styles to use
Serif
Sans Serif

Requirements
Must have
• It must be a really simple and clean design but look edgy.

```html
<!DOCTYPE html>
<html lang="en">
<head>
<meta charset="utf-8">
<title>Forkwise – Find Restaurants Near You</title>
<link rel="stylesheet" href="https://fonts.googleapis.com/css2?family=Catamaran:wght@400;500;600&display=swap">
<style>
  :root {
    --brand-red: #c9202a;
    --backdrop-red: #d12a32;
    --backdrop-deep: #b81d26;
    --ink: #222428;
    --muted: #7b7d80;
    --field-line: #d6d6d6;
    --search-dark: #2e3138;
    --secondary-gray: #8a8a8a;
    --white: #ffffff;
  }
  * { box-sizing: border-box; margin: 0; padding: 0; }
  html, body { width: 1200px; height: 738px; overflow: hidden; }
  body {
    position: relative;
    font-family: "Catamaran", sans-serif;
    color: var(--ink);
    background: var(--backdrop-red);
  }
  .hero-backdrop {
    position: absolute; inset: 0;
    background:
      radial-gradient(circle at 20% 30%, rgba(255,255,255,0.07), transparent 40%),
      radial-gradient(circle at 80% 75%, rgba(255,255,255,0.08), transparent 45%),
      linear-gradient(135deg, var(--backdrop-red), var(--backdrop-deep));
  }
  .site-header {
    position: absolute; top: 0; left: 0; right: 0;
    height: 110px;
    display: flex; justify-content: space-between; align-items: flex-start;
    padding: 38px 64px 0 60px;
  }
  .brand-name {
    display: flex; align-items: center; gap: 10px;
    font-size: 30px; font-weight: 500; color: var(--white);
    line-height: 1; margin-top: 4px;
  }
  .brand-dot {
    width: 34px; height: 34px; border-radius: 50%; background: var(--white);
  }
  .main-nav { display: flex; align-items: center; gap: 12px; font-size: 15px; color: var(--white); margin-top: -6px; }
  .main-nav a { color: var(--white); text-decoration: none; }
  .nav-sep { font-size: 13px; }
  .search-card {
    position: absolute; left: 180px; top: 172px;
    width: 840px; height: 351px;
    background: var(--white); border-radius: 9px;
  }
  .card-badge {
    position: absolute; left: 392px; top: 18px;
    width: 56px; height: 56px; border-radius: 50%;
    background: var(--brand-red);
  }
  .tagline {
    position: absolute; left: 0; right: 0; top: 98px;
    text-align: center; font-size: 21px; font-weight: 400;
    letter-spacing: 0.2px; color: var(--ink);
  }
  .search-field {
    position: absolute; left: 62px; top: 158px;
    width: 571px; height: 48px;
    border: 1px solid var(--field-line); border-radius: 4px;
    display: flex; align-items: center;
  }
  .field-part {
    display: flex; align-items: center; gap: 12px;
    height: 100%; font-size: 16px; color: #3a3c40;
  }
  .field-zip { width: 271px; padding-left: 14px; border-right: 1px solid #9a9a9a; height: 36px; }
  .field-address { padding-left: 14px; }
  .field-part svg { fill: var(--muted); flex: none; }
  .search-button {
    position: absolute; left: 651px; top: 158px;
    width: 123px; height: 47px;
    border: none; border-radius: 4px;
    background: var(--search-dark); color: var(--white);
    font-family: inherit; font-size: 17px; letter-spacing: 0.4px;
  }
  .divider {
    position: absolute; left: 309px; top: 234px; width: 222px; height: 12px;
  }
  .divider::before {
    content: ""; position: absolute; left: 0; right: 0; top: 6px;
    border-top: 1px solid #444;
  }
  .divider-dot {
    position: absolute; left: 104px; top: 0; width: 14px; height: 12px;
    background: var(--white);
  }
  .divider-dot::after {
    content: ""; position: absolute; left: 2px; top: 1px;
    width: 10px; height: 10px; border-radius: 50%; background: var(--brand-red);
  }
  .account-actions {
    position: absolute; top: 277px; left: 0; right: 0;
    display: flex; justify-content: center; gap: 10px; padding-left: 25px;
  }
  .btn {
    height: 42px; border: none; border-radius: 3px;
    color: var(--white); font-family: inherit; font-size: 16px;
  }
  .btn-login { width: 88px; background: var(--brand-red); }
  .btn-create { width: 160px; background: var(--secondary-gray); }
  .site-footer {
    position: absolute; left: 0; right: 0; top: 690px;
    text-align: center; font-size: 16px; color: var(--white);
  }
</style>
</head>
<body>
  <div class="hero-backdrop" role="img" aria-label="Red-tinted photo of people sharing dishes at a restaurant table"></div>

  <header class="site-header">
    <div class="brand-name"><span class="brand-dot"></span>Forkwise</div>
    <nav class="main-nav">
      <a href="#">Order Food</a><span class="nav-sep">|</span><a href="#">Book a Table</a>
    </nav>
  </header>

  <main class="search-card">
    <div class="card-badge"></div>
    <h1 class="tagline">WE HELP PEOPEL FIND RESTAURANTS ARROUND A ZIP CODE OR ADDRESS</h1>

    <form class="search-form">
      <div class="search-field">
        <label class="field-part field-zip">
          <svg width="24" height="26" viewBox="0 0 24 26" aria-hidden="true">
            <path d="M12 1a6 6 0 0 0-6 6c0 4.5 6 11 6 11s6-6.5 6-11a6 6 0 0 0-6-6zm0 8.5A2.5 2.5 0 1 1 12 4.5a2.5 2.5 0 0 1 0 5z"/>
            <path d="M1 25l3-7h4l1 1.5H5l-2 4h18l-2-4h-4l1-1.5h4l3 7z"/>
          </svg>
          Enter Zip Code
        </label>
        <label class="field-part field-address">
          <svg width="20" height="18" viewBox="0 0 20 18" aria-hidden="true">
            <path d="M0 18V6l5-3v3l5-3v3l5-3V0h5v18zM4 10v3h3v-3zm5 0v3h3v-3zm5 0v3h3v-3z"/>
          </svg>
          Enter Address
        </label>
      </div>
      <button class="search-button" type="submit">SEARCH</button>
    </form>

    <div class="divider"><span class="divider-dot"></span></div>

    <div class="account-actions">
      <button class="btn btn-login" type="button">Login</button>
      <button class="btn btn-create" type="button">Create Account</button>
    </div>
  </main>

  <footer class="site-footer">© 2016 Copyright Forkwise All Rights Reserved.</footer>
</body>
</html>
```